Builder of high-end, expensive tables and other furniture

Build a website that represents what we do. I want a luxury feel that appeals to those who can afford our products. We build very high end tables and other furniture using trees that have fallen or are standing dead. We never cut living trees. Trees are harvested, milled, and kiln dried. Then that lumber is meticulously turned into fine furniture using the best equipment. Our furniture prices range from $1,000-$20,000.

Trying to figure out how to raise my spend.

```html
<!DOCTYPE html>
<html lang="en">
<head>
<meta charset="utf-8">
<title>Fallwood Tables LLC</title>
<link rel="stylesheet" href="https://fonts.googleapis.com/css2?family=Barlow+Semi+Condensed:wght@500;600&family=Quicksand:wght@400;500;600&display=swap">
<style>
:root{
  --orange:#ec7038;
  --orange-light:#fd9a6c;
  --orange-pale:#fcc8ae;
  --blue:#2c68a8;
  --blue-deep:#2a63a6;
  --blue-light:#8fb2d8;
  --frame:#8aaed4;
  --ink:#1f1f1f;
  --text:#444;
  --white:#fff;
  --line:#e6e6e6;
}
*{box-sizing:border-box;margin:0;padding:0}
html,body{width:1200px;height:3795px;overflow:hidden}
body{position:relative;background:var(--white);font-family:"Quicksand",sans-serif;color:var(--text)}
.abs{position:absolute}
.heading{font-family:"Barlow Semi Condensed",sans-serif;font-weight:600;color:var(--blue);font-size:36px}
.lead{font-family:"Barlow Semi Condensed",sans-serif;font-weight:500;color:var(--ink);font-size:24px;line-height:34px}
.body-copy{font-size:16.5px;line-height:29px;color:var(--text)}
.btn{display:block;width:156px;height:41px;border-radius:21px;background:var(--orange-light);color:var(--white);font-size:17px;text-align:center;line-height:41px}

/* header */
.site-header{left:0;top:0;width:1200px;height:122px;background:var(--white);border-left:3px solid var(--orange)}
.brand{left:110px;top:42px;font-family:"Quicksand",sans-serif;font-weight:600;font-size:32px;color:var(--orange);display:flex;align-items:center;gap:10px}
.brand-dot{width:14px;height:14px;border-radius:50%;background:var(--orange)}
.nav a{position:absolute;top:50px;font-size:15px;color:#333;text-decoration:none}
.nav a.active{color:var(--orange)}
.cart-badge{left:1066px;top:42px;width:11px;height:11px;border-radius:50%;background:var(--orange)}

/* hero */
.hero-title-sm{left:113px;top:312px;font-size:34px;color:var(--white);font-weight:400}
.hero-title{left:113px;top:352px;font-size:50px;font-family:"Barlow Semi Condensed",sans-serif;font-weight:600;color:var(--white)}
.hero-copy{left:114px;top:424px;font-size:17px;line-height:29px;color:var(--white)}
.hero .btn{left:113px;top:508px;background:var(--orange-light)}
.hero-photo{left:660px;top:225px;width:370px;height:440px;border-radius:50% 50% 12px 12px / 30% 30% 12px 12px;background:radial-gradient(ellipse at 50% 25%,#f4f1ec 0 30%,#c9b08a 55%,rgba(200,130,80,0) 75%)}

/* photo frames */
.frame{border:9px solid var(--frame);border-radius:16px}
.what-photo{left:-16px;top:904px;width:561px;height:350px;background:linear-gradient(160deg,#e9e4dc,#cfc3b2 55%,#8a6a4c)}
.how-photo{left:630px;top:1451px;width:590px;height:349px;background:linear-gradient(180deg,#b9a794,#8f7760 30%,#c2b09a 55%,#7a6350 75%,#c9b9a6)}

/* products */
.card{width:298px;height:366px;background:var(--white);border-radius:10px;box-shadow:0 2px 8px rgba(0,0,0,.14)}
.card-img{position:absolute;left:0;top:0;width:298px;height:233px;border-bottom:1px solid var(--line);border-radius:10px 10px 0 0;overflow:hidden}
.card-img span{position:absolute;left:60px;top:30px;width:178px;height:180px;border-radius:40%;background:radial-gradient(ellipse,#c9a27c 0,#e6d6c4 45%,rgba(255,255,255,0) 70%)}
.heart{position:absolute;right:20px;top:22px}
.card-name{position:absolute;left:20px;top:252px;font-weight:600;font-size:16px;color:var(--ink)}
.card-stars{position:absolute;right:20px;top:252px;font-size:12px;letter-spacing:1px;color:var(--orange)}
.card-desc{position:absolute;left:20px;top:280px;font-size:14px;color:var(--text)}
.card-price{position:absolute;left:22px;top:318px;font-family:"Barlow Semi Condensed",sans-serif;font-weight:600;font-size:22px;color:var(--ink)}
.card-cart{position:absolute;right:20px;top:320px}

/* testimonials */
.review{width:468px;height:277px;background:var(--white);border-radius:10px;box-shadow:0 2px 8px rgba(0,0,0,.12)}
.review p{position:absolute;left:22px;top:30px;width:420px;font-size:16.5px;line-height:29px;color:var(--text)}
.avatar{position:absolute;left:22px;top:172px;width:82px;height:82px;border-radius:50%;background:linear-gradient(#d9c6b4,#8d6e58)}
.reviewer{position:absolute;left:127px;top:196px;font-weight:600;font-size:17px;color:var(--ink)}
.review-stars{position:absolute;left:126px;top:218px;font-size:26px;letter-spacing:2px;color:var(--orange)}
.arrow{width:44px;height:44px;border-radius:50%;background:var(--white);box-shadow:0 1px 6px rgba(0,0,0,.2);display:flex;align-items:center;justify-content:center}

/* footer */
.foot-brand{left:115px;top:3566px;font-weight:600;font-size:44px;color:var(--white);display:flex;align-items:center;gap:12px}
.foot-brand i{width:16px;height:16px;border-radius:50%;background:var(--white)}
.social{top:3649px;width:30px;height:30px;border-radius:50%}
.foot-nav a{position:absolute;top:3580px;font-size:15px;color:var(--white);text-decoration:none}
.subscribe{left:599px;top:3631px;width:494px;height:60px;border-radius:6px;background:var(--white);padding:6px}
.subscribe input{position:absolute;left:22px;top:18px;border:0;font:16px "Quicksand",sans-serif;color:#888;background:none;width:300px}
.subscribe button{position:absolute;right:8px;top:8px;width:108px;height:44px;border:0;border-radius:4px;background:var(--orange);color:var(--white);font:17px "Quicksand",sans-serif}
.copyright{left:0;top:3732px;width:1200px;height:63px;background:var(--white);text-align:center;line-height:63px;font-size:15px;color:#444}
</style>
</head>
<body>

<!-- Hero background -->
<svg class="abs" style="left:0;top:122px" width="1200" height="680" viewBox="0 122 1200 680" aria-hidden="true">
  <path d="M0 122H1200V700C1060 680 900 690 780 735C620 790 380 790 220 740C140 715 70 680 0 670Z" fill="var(--orange-pale)"/>
  <path d="M0 122H1200V688C1060 666 900 676 780 720C620 775 380 775 220 725C140 700 70 668 0 655Z" fill="var(--orange)"/>
  <path d="M1042 122H1200V688C1060 666 900 676 780 720C740 735 705 745 670 752Z" fill="var(--orange-light)"/>
</svg>

<header class="site-header abs">
  <div class="brand abs"><span class="brand-dot"></span>Fallwood Tables</div>
  <nav class="nav">
    <a class="active" style="left:527px" href="#">Home</a>
    <a style="left:602px" href="#">What We Do</a>
    <a style="left:723px" href="#">How We Do</a>
    <a style="left:836px" href="#">Our Products</a>
    <a style="left:960px" href="#">Contact</a>
  </nav>
  <svg class="abs" style="left:1045px;top:48px" width="24" height="22" viewBox="0 0 24 22" aria-label="Cart"><path d="M1 2h4l3 12h12l3-9H7" fill="none" stroke="#111" stroke-width="2.4"/><circle cx="10" cy="19" r="2" fill="#111"/><circle cx="19" cy="19" r="2" fill="#111"/></svg>
  <span class="cart-badge abs"></span>
</header>

<section class="hero">
  <div class="hero-title-sm abs">Welcome to</div>
  <h1 class="hero-title abs">Fallwood Tables llc</h1>
  <p class="hero-copy abs">Lorem ipsum dolor sit amet, consectetur elit,<br>ut labore et dolore aliqua.</p>
  <a class="btn abs" href="#">Get Started</a>
  <div class="hero-photo abs" role="img" aria-label="Round marble-top side table with brass legs, vases and books"></div>
</section>

<section class="what">
  <div class="what-photo frame abs" role="img" aria-label="Living room with a cream sofa and a wooden coffee table"></div>
  <h2 class="heading abs" style="left:602px;top:897px">What We Do</h2>
  <p class="lead abs" style="left:602px;top:960px;width:470px">We build very high end tables and other furniture using trees that have fallen or are standing dead.</p>
  <p class="body-copy abs" style="left:602px;top:1083px;width:495px">Lorem ipsum dolor sit amet, consectetur adipiscing elit, sed do eiusmod tempor incididunt ut labore et dolore magna aliqua. Quis ipsum suspendisse ultrices gravida. Risus commodo viverra maecenas accumsan lacus vel facilisis.</p>
  <a class="btn abs" style="left:599px;top:1230px" href="#">Read More</a>
</section>

<section class="how">
  <h2 class="heading abs" style="left:112px;top:1428px">How We Do</h2>
  <p class="lead abs" style="left:113px;top:1494px;width:490px">We never cut living trees. Trees are harvested, milled, and kiln dried. Then that lumber is meticulously turned into fine furniture using the best equipment.</p>
  <p class="body-copy abs" style="left:113px;top:1650px;width:495px">Lorem ipsum dolor sit amet, consectetur adipiscing elit, sed do eiusmod tempor incididunt ut labore et dolore magna aliqua. Quis ipsum suspendisse ultrices gravida. Risus commodo viverra maecenas accumsan lacus vel facilisis.</p>
  <a class="btn abs" style="left:113px;top:1788px" href="#">Read More</a>
  <div class="how-photo frame abs" role="img" aria-label="Stacked logs with weathered bark"></div>
</section>

<section class="products">
  <h2 class="heading abs" style="left:0;top:1950px;width:1200px;text-align:center">Our Products</h2>

  <article class="card abs" style="left:116px;top:2070px"><div class="card-img" role="img" aria-label="Wooden side table with plant and vase"><span></span></div><svg class="heart" width="20" height="18" viewBox="0 0 20 18"><path d="M10 17 2 9A5 5 0 0 1 10 3 5 5 0 0 1 18 9Z" fill="var(--orange)"/></svg><div class="card-name">Lorem Ipsum</div><div class="card-stars">★★★★★</div><div class="card-desc">Lorem ipsum dolor sit amet,</div><div class="card-price">$1,245.00</div><svg class="card-cart" width="22" height="20" viewBox="0 0 22 20"><path d="M1 2h3l3 11h11l3-8H6" fill="none" stroke="var(--orange)" stroke-width="2"/><circle cx="9" cy="17" r="1.8" fill="var(--orange)"/><circle cx="17" cy="17" r="1.8" fill="var(--orange)"/></svg></article>

  <article class="card abs" style="left:452px;top:2070px"><div class="card-img" role="img" aria-label="Marble-top side table with vases"><span></span></div><svg class="heart" width="20" height="18" viewBox="0 0 20 18"><path d="M10 17 2 9A5 5 0 0 1 10 3 5 5 0 0 1 18 9Z" fill="var(--orange)"/></svg><div class="card-name">Lorem Ipsum</div><div class="card-stars">★★★★★</div><div class="card-desc">Lorem ipsum dolor sit amet,</div><div class="card-price">$1,500.00</div><svg class="card-cart" width="22" height="20" viewBox="0 0 22 20"><path d="M1 2h3l3 11h11l3-8H6" fill="none" stroke="var(--orange)" stroke-width="2"/><circle cx="9" cy="17" r="1.8" fill="var(--orange)"/><circle cx="17" cy="17" r="1.8" fill="var(--orange)"/></svg></article>

  <article class="card abs" style="left:788px;top:2070px"><div class="card-img" role="img" aria-label="Small round table with bent brass legs"><span></span></div><svg class="heart" width="20" height="18" viewBox="0 0 20 18"><path d="M10 17 2 9A5 5 0 0 1 10 3 5 5 0 0 1 18 9Z" fill="var(--orange)"/></svg><div class="card-name">Lorem Ipsum</div><div class="card-stars">★★★★★</div><div class="card-desc">Lorem ipsum dolor sit amet,</div><div class="card-price">$1,745.00</div><svg class="card-cart" width="22" height="20" viewBox="0 0 22 20"><path d="M1 2h3l3 11h11l3-8H6" fill="none" stroke="var(--orange)" stroke-width="2"/><circle cx="9" cy="17" r="1.8" fill="var(--orange)"/><circle cx="17" cy="17" r="1.8" fill="var(--orange)"/></svg></article>

  <article class="card abs" style="left:116px;top:2473px"><div class="card-img" role="img" aria-label="Wooden coffee table with curved legs"><span></span></div><svg class="heart" width="20" height="18" viewBox="0 0 20 18"><path d="M10 17 2 9A5 5 0 0 1 10 3 5 5 0 0 1 18 9Z" fill="var(--orange)"/></svg><div class="card-name">Lorem Ipsum</div><div class="card-stars">★★★★★</div><div class="card-desc">Lorem ipsum dolor sit amet,</div><div class="card-price">$1,145.00</div><svg class="card-cart" width="22" height="20" viewBox="0 0 22 20"><path d="M1 2h3l3 11h11l3-8H6" fill="none" stroke="var(--orange)" stroke-width="2"/><circle cx="9" cy="17" r="1.8" fill="var(--orange)"/><circle cx="17" cy="17" r="1.8" fill="var(--orange)"/></svg></article>

  <article class="card abs" style="left:452px;top:2473px"><div class="card-img" role="img" aria-label="Round table with gold geometric base"><span></span></div><svg class="heart" width="20" height="18" viewBox="0 0 20 18"><path d="M10 17 2 9A5 5 0 0 1 10 3 5 5 0 0 1 18 9Z" fill="var(--orange)"/></svg><div class="card-name">Lorem Ipsum</div><div class="card-stars">★★★★★</div><div class="card-desc">Lorem ipsum dolor sit amet,</div><div class="card-price">$1,684.00</div><svg class="card-cart" width="22" height="20" viewBox="0 0 22 20"><path d="M1 2h3l3 11h11l3-8H6" fill="none" stroke="var(--orange)" stroke-width="2"/><circle cx="9" cy="17" r="1.8" fill="var(--orange)"/><circle cx="17" cy="17" r="1.8" fill="var(--orange)"/></svg></article>

  <article class="card abs" style="left:788px;top:2473px"><div class="card-img" role="img" aria-label="Round wooden table with crossed legs"><span></span></div><svg class="heart" width="20" height="18" viewBox="0 0 20 18"><path d="M10 17 2 9A5 5 0 0 1 10 3 5 5 0 0 1 18 9Z" fill="var(--orange)"/></svg><div class="card-name">Lorem Ipsum</div><div class="card-stars">★★★★★</div><div class="card-desc">Lorem ipsum dolor sit amet,</div><div class="card-price">$1,487.00</div><svg class="card-cart" width="22" height="20" viewBox="0 0 22 20"><path d="M1 2h3l3 11h11l3-8H6" fill="none" stroke="var(--orange)" stroke-width="2"/><circle cx="9" cy="17" r="1.8" fill="var(--orange)"/><circle cx="17" cy="17" r="1.8" fill="var(--orange)"/></svg></article>
</section>

<section class="testimonials">
  <h2 class="heading abs" style="left:0;top:2960px;width:1200px;text-align:center">Testimonials</h2>
  <div class="arrow abs" style="left:40px;top:3180px"><svg width="10" height="14" viewBox="0 0 10 14"><path d="M8 1 2 7l6 6" fill="none" stroke="#111" stroke-width="2.4"/></svg></div>
  <article class="review abs" style="left:116px;top:3062px">
    <p>Lorem ipsum dolor sit amet, consectetur adipiscing elit, sed do eiusmod tempor incididunt ut labore et dolore magna aliqua. Quis ipsum suspendisse ultrices gravida.</p>
    <div class="avatar" role="img" aria-label="Portrait of Daniel Reyes"></div>
    <div class="reviewer">Daniel Reyes</div>
    <div class="review-stars">★★★★★</div>
  </article>
  <article class="review abs" style="left:617px;top:3062px">
    <p>Lorem ipsum dolor sit amet, consectetur adipiscing elit, sed do eiusmod tempor incididunt ut labore et dolore magna aliqua. Quis ipsum suspendisse ultrices gravida.</p>
    <div class="avatar" role="img" aria-label="Portrait of Maya Collins"></div>
    <div class="reviewer">Maya Collins</div>
    <div class="review-stars">★★★★★</div>
  </article>
  <div class="arrow abs" style="left:1122px;top:3180px"><svg width="10" height="14" viewBox="0 0 10 14"><path d="M2 1l6 6-6 6" fill="none" stroke="#111" stroke-width="2.4"/></svg></div>
</section>

<footer>
  <svg class="abs" style="left:0;top:3395px" width="1200" height="337" viewBox="0 3395 1200 337" aria-hidden="true">
    <path d="M0 3520C150 3470 300 3400 480 3402C680 3405 800 3480 960 3497C1060 3507 1140 3498 1200 3488V3732H0Z" fill="var(--blue-light)"/>
    <path d="M0 3532C150 3482 300 3412 480 3414C680 3417 800 3492 960 3509C1060 3519 1140 3510 1200 3500V3732H0Z" fill="var(--blue-deep)"/>
    <path d="M560 3732 720 3440C800 3480 880 3505 960 3509C1060 3519 1140 3510 1200 3500V3732Z" fill="#3a76b8"/>
  </svg>
  <div class="foot-brand abs"><i></i>Fallwood Tables</div>
  <span class="social abs" style="left:169px;background:#3b5a9a" aria-label="Social link"></span>
  <span class="social abs" style="left:218px;background:#d9347a" aria-label="Social link"></span>
  <span class="social abs" style="left:266px;background:#1d5fa0" aria-label="Social link"></span>
  <span class="social abs" style="left:315px;background:#2b9be8" aria-label="Social link"></span>
  <nav class="foot-nav">
    <a style="left:602px" href="#">Home</a>
    <a style="left:677px" href="#">What We Do</a>
    <a style="left:798px" href="#">How We Do</a>
    <a style="left:911px" href="#">Our Products</a>
    <a style="left:1035px" href="#">Contact</a>
  </nav>
  <form class="subscribe abs">
    <input type="email" placeholder="Email" aria-label="Email">
    <button type="button">Submit</button>
  </form>
  <div class="copyright abs">Copyright © 2023 Fallwood Tables LLC | &nbsp;All Rights Reserved.</div>
</footer>

</body>
</html>
```